KDWB Business Card

Looking for a business card design to incorporate our branding. We want to only use the colors listing in the Branding Package (attached).
Updates

Target Market(s)

People who need their phone or device fixed.

Industry/Entity Type

Electronics

Contact Information for Business Card

Please use:

Brightwick Gadget Clinic LLC
4810 E Harlow Ridge Rd
Suite 417
San Antonio, TX 78163

Marcus Delgrove, Store Manager

(210) 555-0147

Requirements
Must have
• Must include the colors that are contained within the Branding Package PDF file.

```html
<!DOCTYPE html>
<html lang="en">
<head>
<meta charset="utf-8">
<title>Brightwick Gadget Clinic Business Card</title>
<link rel="stylesheet" href="https://fonts.googleapis.com/css2?family=Arimo:wght@400;700&display=swap">
<style>
  :root {
    --bg: #2b2d31;
    --card: #ffffff;
    --orange: #f05a28;
    --ink: #2a2a2a;
    --band: #5e5f62;
    --band-text: #ffffff;
    --rule: #6d6d6d;
  }
  * { box-sizing: border-box; margin: 0; padding: 0; }
  html, body {
    width: 1200px; height: 960px; overflow: hidden;
    background: var(--bg);
    font-family: "Arimo", Arial, sans-serif;
  }
  .canvas { position: relative; width: 1200px; height: 960px; }
  .card {
    position: absolute; left: 285px; width: 630px; height: 360px;
    background: var(--card);
    box-shadow: 0 10px 30px rgba(0,0,0,.45);
    overflow: hidden;
  }
  .card--front { top: 90px; }
  .card--back { top: 510px; }

  .brand { display: flex; align-items: center; gap: 12px; }
  .brand__square { width: 34px; height: 34px; background: var(--orange); border-radius: 6px; }
  .brand__name { color: var(--orange); font-size: 30px; font-weight: 400; white-space: nowrap; }

  .card--front .brand { position: absolute; left: 50%; top: 50%; transform: translate(-50%, -50%); }

  .card--back .brand { position: absolute; left: 40px; top: 142px; }
  .card--back .brand__name { font-size: 22px; }
  .card--back .brand__square { width: 28px; height: 28px; }

  .divider { position: absolute; left: 336px; top: 0; width: 1px; height: 300px; background: var(--rule); }

  .person { position: absolute; left: 366px; top: 38px; }
  .person__name { font-size: 24px; color: var(--ink); }
  .person__title { font-size: 14px; color: var(--orange); margin-top: 2px; }

  .contact { position: absolute; left: 366px; top: 160px; list-style: none; font-size: 15px; color: var(--ink); }
  .contact__item { display: flex; align-items: center; gap: 10px; margin-bottom: 12px; }
  .contact__item--gap { margin-bottom: 26px; }
  .contact__icon { width: 16px; height: 16px; flex: none; }

  .address-band {
    position: absolute; left: 0; bottom: 0; width: 100%; height: 60px;
    background: var(--band); color: var(--band-text);
    display: flex; align-items: center; justify-content: center;
    font-size: 19px; letter-spacing: .5px;
  }
</style>
</head>
<body>
<main class="canvas">
  <section class="card card--front" aria-label="Card front">
    <div class="brand">
      <span class="brand__square"></span>
      <span class="brand__name">Brightwick Gadget Clinic</span>
    </div>
  </section>

  <section class="card card--back" aria-label="Card back">
    <div class="brand">
      <span class="brand__square"></span>
      <span class="brand__name">Brightwick Gadget Clinic</span>
    </div>
    <div class="divider"></div>
    <div class="person">
      <p class="person__name">Marcus Delgrove</p>
      <p class="person__title">Store Manager</p>
    </div>
    <ul class="contact">
      <li class="contact__item contact__item--gap">
        <svg class="contact__icon" viewBox="0 0 16 16"><rect width="16" height="16" rx="2" fill="#f05a28"/><path d="M5 3.5c.6 0 1.4 1.6 1.4 2.1 0 .6-.8.8-.8 1.2 0 .8 1.7 2.5 2.5 2.5.4 0 .6-.8 1.2-.8.5 0 2.1.8 2.1 1.4 0 .8-1 1.8-2 1.8C6.8 11.7 4.3 9.2 3.2 6 3.2 5 4.2 3.5 5 3.5z" fill="#fff"/></svg>
        <span>(210) 555-0147</span>
      </li>
      <li class="contact__item">
        <svg class="contact__icon" viewBox="0 0 16 16"><rect width="16" height="16" rx="2" fill="#f05a28"/><rect x="3" y="4.5" width="10" height="7" fill="none" stroke="#fff" stroke-width="1.2"/><path d="M3 4.5l5 4 5-4" fill="none" stroke="#fff" stroke-width="1.2"/></svg>
        <span>marcus@BrightwickClinic.com</span>
      </li>
      <li class="contact__item">
        <svg class="contact__icon" viewBox="0 0 16 16"><rect width="16" height="16" rx="2" fill="#f05a28"/><circle cx="8" cy="8" r="4.5" fill="none" stroke="#fff" stroke-width="1.2"/><path d="M3.5 8h9M8 3.5c-2 2.5-2 6.5 0 9M8 3.5c2 2.5 2 6.5 0 9" fill="none" stroke="#fff" stroke-width="1"/></svg>
        <span>www.BrightwickClinic.com</span>
      </li>
    </ul>
    <div class="address-band">4810 E Harlow Ridge Rd, Suite 417, San Antonio, TX 78163</div>
  </section>
</main>
</body>
</html>
```